Business card design for Automotive workshop

We need a business card for a new automotive repair and tyre shop called Keelstone Prime Automotive located in New Zealand. We are a clean, modern and fresh workshop and company.

Front needs to feature logo,
my name:
Marlo Fenwicke (director)

Address:
48 Tarn Lane
Whitianga 3510

Phone: 07 594 2713
Mobile: 027 451 9362
Email: office@keelstoneautomotive.example.nz
Website: keelstoneautomotive.example.nz

Back needs to feature an area to write down appointment details, date and time.

Also feature a list of jobs and work we do such as,
Vehicle Servicing
All Mechanical Repairs
Warrant of Fitness
Tyres & Wheel Alignments
Automotive Diagnostics
Automotive Parts & Supplies

```html
<!DOCTYPE html>
<html lang="en">
<head>
<meta charset="utf-8">
<title>Keelstone Prime Automotive – Business Card</title>
<link rel="stylesheet" href="https://fonts.googleapis.com/css2?family=Montserrat:wght@600;700;800&family=Open+Sans:wght@400;600&display=swap">
<style>
  :root {
    --ink: #111111;
    --panel: #303030;
    --red: #e61e29;
    --white: #ffffff;
    --muted: #d9d9d9;
    --rule: #8a8a8a;
    --backdrop: #d2d1cc;
  }
  * { box-sizing: border-box; margin: 0; padding: 0; }
  html, body { width: 1200px; height: 801px; overflow: hidden; }
  body {
    background: var(--backdrop);
    display: flex;
    align-items: center;
    justify-content: center;
    gap: 24px;
    font-family: "Open Sans", Arial, sans-serif;
  }
  .card {
    position: relative;
    width: 560px;
    height: 320px;
    background: var(--ink);
    overflow: hidden;
    box-shadow: 0 10px 26px rgba(0,0,0,0.25);
  }

  /* Front */
  .brand {
    position: absolute;
    left: 34px;
    top: 112px;
    width: 220px;
    display: flex;
    align-items: center;
    gap: 10px;
  }
  .brand-mark { width: 16px; height: 16px; background: var(--red); flex: none; }
  .brand-name {
    font-family: "Montserrat", Arial, sans-serif;
    font-weight: 800;
    font-size: 21px;
    line-height: 1.1;
    color: var(--red);
    text-transform: uppercase;
    letter-spacing: 0.5px;
  }
  .divider {
    position: absolute;
    left: 272px;
    top: 52px;
    width: 1px;
    height: 140px;
    background: var(--rule);
  }
  .person { position: absolute; left: 292px; top: 46px; }
  .person-name {
    font-family: "Montserrat", Arial, sans-serif;
    font-weight: 700;
    font-size: 22px;
    color: var(--red);
  }
  .person-role { font-size: 12px; color: var(--white); margin-top: 2px; }
  .contacts { list-style: none; margin-top: 14px; }
  .contacts li {
    display: flex;
    align-items: center;
    gap: 7px;
    font-size: 11.5px;
    line-height: 19px;
    color: var(--white);
    white-space: nowrap;
  }
  .contacts svg { width: 10px; height: 10px; flex: none; }
  .swoosh { position: absolute; left: 0; bottom: 0; }
  .address {
    font-family: "Open Sans", Arial, sans-serif;
    font-size: 12.5px;
    fill: var(--white);
  }

  /* Back */
  .appt-title {
    position: absolute;
    left: 150px;
    top: 26px;
    font-family: "Montserrat", Arial, sans-serif;
    font-weight: 700;
    font-size: 21px;
    color: var(--red);
  }
  .writing-area {
    position: absolute;
    left: 22px;
    right: 22px;
    top: 64px;
    height: 118px;
    background: var(--panel);
  }
  .fields {
    position: absolute;
    left: 26px;
    right: 26px;
    top: 194px;
    display: flex;
    gap: 18px;
    align-items: flex-end;
  }
  .field { flex: 1; display: flex; align-items: flex-end; gap: 8px; }
  .field-label {
    font-family: "Montserrat", Arial, sans-serif;
    font-weight: 700;
    font-size: 14px;
    color: var(--white);
  }
  .field-line { flex: 1; border-bottom: 1px dashed var(--muted); margin-bottom: 4px; }
  .works-band {
    position: absolute;
    left: 0; right: 0; bottom: 0;
    height: 86px;
    background: var(--red);
  }
  .works-pill {
    position: absolute;
    left: 50%;
    top: -14px;
    transform: translateX(-50%);
    padding: 4px 26px;
    border-radius: 14px;
    background: var(--red);
    border: 2px solid var(--ink);
    font-family: "Montserrat", Arial, sans-serif;
    font-weight: 700;
    font-size: 15px;
    color: var(--white);
  }
  .services {
    list-style: none;
    position: absolute;
    left: 18px; right: 18px; top: 26px;
    display: flex;
    flex-wrap: wrap;
    justify-content: center;
    column-gap: 14px;
    row-gap: 4px;
  }
  .services li { font-size: 12px; color: var(--white); white-space: nowrap; }
  .services li::before { content: "● "; font-size: 8px; vertical-align: 2px; }
</style>
</head>
<body>

<section class="card card-front" aria-label="Card front">
  <div class="brand">
    <span class="brand-mark"></span>
    <span class="brand-name">Keelstone Prime Automotive</span>
  </div>

  <div class="divider"></div>

  <div class="person">
    <p class="person-name">Marlo Fenwicke</p>
    <p class="person-role">Director</p>
    <ul class="contacts">
      <li>
        <svg viewBox="0 0 10 10"><path d="M2 1l2 2-1 1.2c.6 1.3 1.5 2.2 2.8 2.8L7 6l2 2-1.2 1.3C4.5 9 1 5.5.7 2.2z" fill="var(--red)"/></svg>
        07 594 2713
      </li>
      <li>
        <svg viewBox="0 0 10 10"><rect x="2.5" y="0.5" width="5" height="9" rx="1" fill="none" stroke="var(--red)"/><circle cx="5" cy="8" r=".6" fill="var(--red)"/></svg>
        027 451 9362
      </li>
      <li>
        <svg viewBox="0 0 10 10"><rect x=".5" y="1.5" width="9" height="7" fill="var(--red)"/><path d="M.5 2l4.5 3.5L9.5 2" fill="none" stroke="var(--ink)"/></svg>
        office@keelstoneautomotive.example.nz
      </li>
      <li>
        <svg viewBox="0 0 10 10"><circle cx="5" cy="5" r="4.3" fill="none" stroke="var(--red)"/><path d="M.7 5h8.6M5 .7c-2.2 2.6-2.2 6 0 8.6M5 .7c2.2 2.6 2.2 6 0 8.6" fill="none" stroke="var(--red)" stroke-width=".8"/></svg>
        keelstoneautomotive.example.nz
      </li>
    </ul>
  </div>

  <svg class="swoosh" width="560" height="320" viewBox="0 0 560 320">
    <defs>
      <path id="address-path" d="M40,314 Q280,262 540,304"/>
    </defs>
    <path d="M0,320 Q280,238 560,312 L560,320 Z" fill="var(--red)"/>
    <text class="address"><textPath href="#address-path" startOffset="22%">48 Tarn Lane Whitianga 3510</textPath></text>
  </svg>
</section>

<section class="card card-back" aria-label="Card back">
  <h2 class="appt-title">Appointment Details</h2>
  <div class="writing-area"></div>

  <div class="fields">
    <div class="field"><span class="field-label">Date</span><span class="field-line"></span></div>
    <div class="field"><span class="field-label">Time</span><span class="field-line"></span></div>
  </div>

  <div class="works-band">
    <span class="works-pill">Our Works</span>
    <ul class="services">
      <li>Vehicle Servicing</li>
      <li>Warrant of Fitness</li>
      <li>Automotive Parts &amp; Supplies</li>
      <li>Automotive Diagnostics</li>
      <li>Tyres &amp; Wheel Alignments</li>
      <li>All Mechanical Repairs</li>
    </ul>
  </div>
</section>

</body>
</html>
```